Simple and Clean business card design

We would like the design to be simple clean and to incorporate our colors.

We are open to your design and talent, we have the dots in our logo as we think of it as data points and we connect data points for people.

We are open to see the great creative and clean design you bring to the table

Contact Information for Business Card

please include: name, position, email, phone and website

Font styles to use
Sans Serif

Requirements
Must have
• my colors incorporated, simplicity
Nice to have
• lots of white space, simplicity
Should not have
• complexicity/ complex art

```html
<!DOCTYPE html>
<html lang="en">
<head>
<meta charset="UTF-8">
<title>Clustra Business Card</title>
<link rel="stylesheet" href="https://fonts.googleapis.com/css2?family=Montserrat:wght@400;600;700&display=swap">
<style>
  :root {
    --canvas-bg: #e6e6e6;
    --card-white: #f7f7f7;
    --card-black: #0d0d0d;
    --ink: #111111;
    --paper-ink: #ffffff;
    --green: #34a853;
    --yellow: #fbbc05;
    --red: #ea4335;
    --blue: #4285f4;
    --rule: #555555;
  }
  * { box-sizing: border-box; margin: 0; padding: 0; }
  html, body {
    width: 1200px;
    height: 930px;
    overflow: hidden;
    background: var(--canvas-bg);
    font-family: "Montserrat", Arial, sans-serif;
  }
  .stage {
    position: relative;
    width: 1200px;
    height: 930px;
    display: flex;
    align-items: center;
    justify-content: center;
    gap: 60px;
  }
  .card {
    position: relative;
    width: 520px;
    height: 297px;
    border-radius: 3px;
    box-shadow: 0 10px 28px rgba(0,0,0,0.16), 0 2px 5px rgba(0,0,0,0.1);
    overflow: hidden;
  }
  .card--front { background: var(--card-white); color: var(--ink); }
  .card--back { background: var(--card-black); color: var(--paper-ink); }

  .wordmark {
    position: absolute;
    display: flex;
    align-items: flex-start;
    gap: 10px;
    font-weight: 700;
    letter-spacing: 1px;
    line-height: 1;
  }
  .wordmark__name { font-size: 74px; }
  .wordmark__dot {
    width: 24px;
    height: 24px;
    border-radius: 50%;
    background: var(--green);
    margin-top: 4px;
  }
  .card--front .wordmark { left: 92px; top: 62px; }
  .card--back .wordmark { left: 50%; top: 50%; transform: translate(-50%, -50%); }

  .identity {
    position: absolute;
    left: 56px;
    top: 198px;
  }
  .identity__name {
    font-weight: 700;
    font-size: 17px;
    letter-spacing: 0.2px;
  }
  .identity__role {
    font-weight: 400;
    font-size: 13px;
    margin-top: 3px;
  }
  .divider {
    position: absolute;
    left: 214px;
    top: 194px;
    width: 1px;
    height: 64px;
    background: var(--rule);
  }
  .contacts {
    position: absolute;
    left: 230px;
    top: 194px;
    list-style: none;
    font-size: 13px;
    font-weight: 400;
  }
  .contacts__item {
    display: flex;
    align-items: center;
    gap: 8px;
    height: 21px;
  }
  .contacts__icon {
    width: 15px;
    height: 15px;
    flex: none;
  }
  .contacts__accent { color: var(--blue); }
</style>
</head>
<body>
<main class="stage">
  <section class="card card--front" aria-label="Business card front">
    <div class="wordmark">
      <span class="wordmark__name">Clustra</span>
      <span class="wordmark__dot"></span>
    </div>

    <div class="identity">
      <p class="identity__name">Dana Whitlow</p>
      <p class="identity__role">Founder/ CEO</p>
    </div>

    <div class="divider"></div>

    <ul class="contacts">
      <li class="contacts__item">
        <svg class="contacts__icon" viewBox="0 0 16 16" aria-hidden="true">
          <circle cx="8" cy="8" r="8" fill="var(--green)"/>
          <path d="M5.6 4.2l1.3 1.6-.7.9c.4.9 1.2 1.7 2.1 2.1l.9-.7 1.6 1.3-.6 1.3c-2.8-.3-5.1-2.6-5.4-5.4z" fill="#fff"/>
        </svg>
        <span>555-204-1187</span>
      </li>
      <li class="contacts__item">
        <svg class="contacts__icon" viewBox="0 0 16 16" aria-hidden="true">
          <circle cx="8" cy="8" r="8" fill="var(--yellow)"/>
          <rect x="4" y="5.2" width="8" height="5.6" fill="none" stroke="#fff" stroke-width="1.1"/>
          <path d="M4 5.4l4 3 4-3" fill="none" stroke="#fff" stroke-width="1.1"/>
        </svg>
        <span>dana.whitlow@clustra.io</span>
      </li>
      <li class="contacts__item">
        <svg class="contacts__icon" viewBox="0 0 16 16" aria-hidden="true">
          <circle cx="8" cy="8" r="8" fill="var(--red)"/>
          <circle cx="8" cy="8" r="4" fill="none" stroke="#fff" stroke-width="1"/>
          <ellipse cx="8" cy="8" rx="1.8" ry="4" fill="none" stroke="#fff" stroke-width="0.9"/>
          <path d="M4 8h8" stroke="#fff" stroke-width="0.9"/>
        </svg>
        <span>www.<span class="contacts__accent">clustra</span>.io</span>
      </li>
    </ul>
  </section>

  <section class="card card--back" aria-label="Business card back">
    <div class="wordmark">
      <span class="wordmark__name">Clustra</span>
      <span class="wordmark__dot"></span>
    </div>
  </section>
</main>
</body>
</html>
```